RESIDENTIAL CONSTRUCTION

We are a company that specializes in building custom residential homes, the design should also emphasize that quality and service is our priority.

Industry/Entity Type

Construction Company

Contact Information for Business Card

Contact Person: Marcus Lindqvist
Company Address: 273 West Alder Ave San Jose , Ca 95380
Phone Number : 408-731-2946
Email Address: Stoneridgehomes517@mailvista.net

Font styles to use
Sans Serif

Colors
ec1f27

Requirements
Must have
• CSLB # 7362015
Nice to have
• needs to have same color as logo i uploaded, we will be printing these on a clear plastic card.

```html
<!DOCTYPE html>
<html lang="en">
<head>
<meta charset="utf-8">
<title>Stoneridge Homes – Business Card</title>
<link rel="stylesheet" href="https://fonts.googleapis.com/css2?family=Bebas+Neue&family=Arimo:wght@400&display=swap">
<style>
  :root {
    --page-bg: #d9d6d2;
    --card-top: #f4f3f1;
    --card-bottom: #e6e4e1;
    --brand-red: #9a1419;
    --ink: #1c1c1c;
  }
  * { margin: 0; padding: 0; box-sizing: border-box; }
  html, body { width: 1200px; height: 970px; overflow: hidden; background: var(--page-bg); }
  .canvas { position: relative; width: 1200px; height: 970px; }
  .card {
    position: absolute; left: 80px; top: 190px; width: 1040px; height: 590px;
    border-radius: 28px; overflow: hidden;
    background: linear-gradient(180deg, var(--card-top), var(--card-bottom));
    box-shadow: 0 18px 40px rgba(0,0,0,.18);
  }
  .card-wave { position: absolute; left: 0; top: 0; width: 1040px; height: 590px; }
  .brand {
    position: absolute; left: 66px; top: 232px; display: flex; align-items: center; gap: 14px;
  }
  .brand-mark { width: 52px; height: 52px; background: var(--brand-red); flex: none; }
  .brand-name {
    font-family: "Bebas Neue", sans-serif; font-weight: 400; font-size: 62px; line-height: 1;
    color: var(--brand-red); letter-spacing: .5px; white-space: nowrap;
  }
  .divider { position: absolute; left: 517px; top: 150px; width: 2px; height: 250px; background: var(--brand-red); }
  .contact { position: absolute; left: 556px; top: 142px; color: var(--ink); font-family: "Arimo", sans-serif; }
  .contact-name { font-family: "Bebas Neue", sans-serif; font-weight: 400; font-size: 44px; letter-spacing: .5px; line-height: 1; margin-bottom: 20px; }
  .contact-address { font-size: 23px; line-height: 37px; margin-bottom: 6px; }
  .contact-row { display: flex; align-items: center; gap: 12px; font-size: 23px; height: 42px; }
  .contact-icon { width: 32px; height: 32px; flex: none; }
  .contact-license { font-size: 20px; line-height: 1; margin-top: 8px; }
</style>
</head>
<body>
<main class="canvas">
  <section class="card">
    <svg class="card-wave" viewBox="0 0 1040 590" aria-hidden="true">
      <defs>
        <linearGradient id="bandFill" x1="0" y1="0" x2="1" y2="0">
          <stop offset="0" stop-color="#a11a1f"/>
          <stop offset=".5" stop-color="#8c1015"/>
          <stop offset="1" stop-color="#a3191e"/>
        </linearGradient>
        <linearGradient id="swooshFill" x1="0" y1="0" x2="1" y2="0">
          <stop offset="0" stop-color="#6b6767" stop-opacity=".3"/>
          <stop offset=".5" stop-color="#3a3636"/>
          <stop offset="1" stop-color="#5a5555"/>
        </linearGradient>
      </defs>
      <path d="M0,468 C180,490 380,560 600,540 C790,520 900,462 1040,458 L1040,590 L0,590 Z" fill="url(#bandFill)"/>
      <path d="M10,462 C200,500 420,548 620,520 C800,494 900,448 1030,446 C900,458 800,508 620,536 C420,566 200,520 10,462 Z" fill="url(#swooshFill)"/>
    </svg>

    <div class="brand">
      <div class="brand-mark"></div>
      <span class="brand-name">STONERIDGE HOMES</span>
    </div>

    <div class="divider"></div>

    <div class="contact">
      <h1 class="contact-name">MARCUS LINDQVIST</h1>
      <p class="contact-address">273 West Alder Ave<br>San Jose, Ca 95380</p>
      <p class="contact-row">
        <svg class="contact-icon" viewBox="0 0 32 32" aria-hidden="true">
          <circle cx="16" cy="16" r="16" fill="var(--brand-red)"/>
          <path d="M11 9 l3 0 l1.5 4 l-2 1.5 c1 2.2 2.8 4 5 5 l1.5-2 l4 1.5 l0 3 c-7 1-14-6-13-13z" fill="#fff"/>
        </svg>
        408-731-2946
      </p>
      <p class="contact-row">
        <svg class="contact-icon" viewBox="0 0 32 32" aria-hidden="true">
          <circle cx="16" cy="16" r="16" fill="var(--brand-red)"/>
          <rect x="8.5" y="10.5" width="15" height="11" fill="none" stroke="#fff" stroke-width="1.8"/>
          <path d="M8.5 10.5 L16 17 L23.5 10.5" fill="none" stroke="#fff" stroke-width="1.8"/>
        </svg>
        Stoneridgehomes517@mailvista.net
      </p>
      <p class="contact-license">CSLB # 7362015</p>
    </div>
  </section>
</main>
</body>
</html>
```